NCBG website design

We need a page template website design for a cms website. Please see the brief attached for the details.
The client is the National Copperfleece Breeders Guild which is an organisation promoting the Copperfleece Sheep Breed within Australia.
Updates

Project Deadline Extended
Reason: So that my top few designs can make changes and re-submit.

Target Market(s)

See attached brief

```html
<!DOCTYPE html>
<html lang="en">
<head>
<meta charset="utf-8">
<title>National Copperfleece Breeders Guild</title>
<link href="https://fonts.googleapis.com/css2?family=Open+Sans:wght@400;600;700&display=swap" rel="stylesheet">
<style>
:root{
  --green:#17623f;
  --green-light:#4f9a6c;
  --yellow:#f6c42a;
  --page:#e9e8e6;
  --ink:#333;
  --muted:#555;
  --footer:#1b1b1b;
  --white:#fff;
}
*{box-sizing:border-box;margin:0;padding:0}
html,body{width:929px;height:1200px;overflow:hidden}
body{position:relative;background:var(--page);font-family:Arial,Helvetica,sans-serif;color:var(--ink)}
.site-header{position:absolute;left:0;top:0;width:929px;height:102px;background:var(--white)}
.brand{position:absolute;left:80px;top:32px;display:flex;align-items:center;gap:9px}
.brand-mark{width:32px;height:32px;background:var(--green);border-radius:4px}
.brand-name{font-family:"Open Sans",sans-serif;font-weight:700;font-size:27px;line-height:36px;color:var(--green);letter-spacing:-.5px}
.call{position:absolute;right:81px;top:16px;font-size:11px;display:flex;align-items:baseline;gap:4px}
.call strong{font-weight:400;font-size:18px}
.main-nav{position:absolute;left:0;top:102px;width:929px;height:36px;background:var(--green)}
.main-nav a{position:absolute;top:0;line-height:36px;color:var(--white);font-size:10px;font-weight:700;text-decoration:none;text-transform:uppercase}
.main-nav a.active{top:5px;line-height:26px;height:26px;width:65px;text-align:center;background:#2a2a2a;border:1px solid #555;border-radius:3px}
.hero{position:absolute;left:0;top:138px;width:929px;height:343px;background:linear-gradient(100deg,#8a7a6a 0%,#c9c2b6 30%,#b8ae9f 55%,#a59b8d 80%,#8e8376 100%)}
.feature{position:absolute;top:428px;width:167px;height:214px;background:linear-gradient(#dcdcdc 0%,#f9f9f9 45%,#fff 100%);border-top:7px solid var(--yellow);border-radius:0 0 8px 8px;box-shadow:0 1px 3px rgba(0,0,0,.1);text-align:center}
.feature-icon{width:76px;height:76px;margin:26px auto 0;border-radius:50%;background:#fff;border:7px solid #e8e8e8;display:flex;align-items:center;justify-content:center}
.feature h3{font-family:"Open Sans",sans-serif;font-size:13.5px;font-weight:700;margin-top:28px;color:#333}
.feature p{font-size:13px;color:var(--muted);margin-top:2px}
.feature a{display:block;font-size:8px;font-style:italic;color:#e0a800;text-decoration:none;margin-top:9px}
.tabs{position:absolute;left:102px;top:669px;display:flex;gap:4px}
.tab{height:34px;line-height:34px;padding-left:12px;font-family:"Open Sans",sans-serif;font-size:14px;font-weight:600;color:#555;background:linear-gradient(#f2f2f2,#e4e4e4);border:1px solid #ccc;border-bottom:none}
.tab.active{background:linear-gradient(var(--green-light),var(--green));color:#fff;padding-left:0;text-align:center;border-color:var(--green)}
.tab-panel{position:absolute;left:102px;top:702px;width:731px;height:188px;background:linear-gradient(#f5f5f5,#e6e6e6);border:1px solid #ccc;border-radius:0 0 4px 4px}
.tab-photo{position:absolute;left:16px;top:25px;width:166px;height:128px;border:6px solid var(--yellow);background:linear-gradient(#5d7a3c,#8aa25a 50%,#c9c4b1 70%,#6f8a43)}
.tab-copy{position:absolute;left:196px;top:29px;width:515px;font-size:9.6px;line-height:15.6px;color:#444}
.tab-copy p+p{margin-top:15px}
.sponsors{position:absolute;left:104px;top:953px;width:730px;height:91px;border:1px solid #ccc;background:var(--page)}
.sponsors-title{position:absolute;left:399px;top:928px;width:129px;height:38px;background:var(--page);border:1px solid #ccc;border-bottom:none;text-align:center;line-height:38px;font-family:"Open Sans",sans-serif;font-weight:600;font-size:16px;color:var(--green)}
.sponsor{position:absolute;top:996px;transform:translateY(-50%)}
.site-footer{position:absolute;left:0;top:1069px;width:929px;height:131px;background:var(--footer);text-align:center;border-bottom:5px solid var(--green)}
.footer-nav{margin-top:13px;font-family:"Open Sans",sans-serif;font-size:8.5px;color:#bbb}
.footer-nav a{color:#bbb;text-decoration:none}
.footer-nav span{margin:0 5px}
.connect{display:inline-flex;align-items:center;gap:6px;margin-top:20px;height:20px;padding:0 6px 0 4px;background:#4a67a8;border:1px solid #7a93c8;color:#fff;font-family:"Open Sans",sans-serif;font-weight:700;font-size:11px}
.connect i{width:13px;height:13px;background:#fff;border-radius:2px;display:block}
.legal{margin-top:10px;font-size:9px;line-height:14.5px;color:#bbb}
</style>
</head>
<body>
<header class="site-header">
  <div class="brand"><span class="brand-mark"></span><span class="brand-name">Copperfleece</span></div>
  <div class="call">
    <svg width="10" height="12" viewBox="0 0 10 12"><path d="M2 0 L4 3 L3 4.5 Q4 7 6 8.5 L7.5 7.5 L10 10 L8 12 Q2 10 0 2 Z" fill="#333"/></svg>
    <span>Call us :</span><strong>08 7000 4182</strong>
  </div>
</header>

<nav class="main-nav">
  <a class="active" href="#" style="left:90px">Home</a>
  <a href="#" style="left:206px">About</a>
  <a href="#" style="left:313px">Search</a>
  <a href="#" style="left:438px">Stud Pages</a>
  <a href="#" style="left:576px">Sales</a>
  <a href="#" style="left:681px">Links</a>
  <a href="#" style="left:797px">Contact</a>
</nav>

<div class="hero" role="img" aria-label="Photo of Copperfleece sheep standing in a shearing shed"></div>

<section class="feature" style="left:107px">
  <div class="feature-icon"><svg width="26" height="26" viewBox="0 0 26 26"><path d="M3 4h20v13H11l-6 5v-5H3z" fill="none" stroke="#17623f" stroke-width="2.2" stroke-linejoin="round"/><circle cx="9" cy="10.5" r="1.4" fill="#17623f"/><circle cx="13" cy="10.5" r="1.4" fill="#17623f"/><circle cx="17" cy="10.5" r="1.4" fill="#17623f"/></svg></div>
  <h3>Prime Lamb Helpline</h3><p>Lorem Ipsum dolor.</p><a href="#">read more</a>
</section>
<section class="feature" style="left:286px">
  <div class="feature-icon"><svg width="24" height="24" viewBox="0 0 24 24"><rect x="2" y="4" width="20" height="18" fill="#17623f"/><rect x="6" y="1" width="2" height="5" fill="#17623f"/><rect x="16" y="1" width="2" height="5" fill="#17623f"/><g fill="#fff"><rect x="5" y="10" width="3" height="2.5"/><rect x="10.5" y="10" width="3" height="2.5"/><rect x="16" y="10" width="3" height="2.5"/><rect x="5" y="15.5" width="3" height="2.5"/><rect x="10.5" y="15.5" width="3" height="2.5"/><rect x="16" y="15.5" width="3" height="2.5"/></g></svg></div>
  <h3>Events</h3><p>Lorem Ipsum dolor.</p><a href="#">read more</a>
</section>
<section class="feature" style="left:467px">
  <div class="feature-icon"><svg width="24" height="24" viewBox="0 0 24 24"><circle cx="10" cy="6" r="4.5" fill="#17623f"/><path d="M2 22 Q2 12 10 12 Q18 12 18 22Z" fill="#17623f"/><path d="M17 14v8M13 18h8" stroke="#fff" stroke-width="4"/><path d="M17 14v8M13 18h8" stroke="#17623f" stroke-width="2"/></svg></div>
  <h3>Members</h3><p>Lorem Ipsum dolor.</p><a href="#">read more</a>
</section>
<section class="feature" style="left:653px">
  <div class="feature-icon"><svg width="26" height="22" viewBox="0 0 26 22"><rect x="1" y="1" width="24" height="20" rx="2" fill="none" stroke="#17623f" stroke-width="2"/><rect x="5" y="5" width="7" height="6" fill="#17623f"/><path d="M14 6h7M14 10h7M5 15h16" stroke="#17623f" stroke-width="2"/></svg></div>
  <h3>Latest News</h3><p>Lorem Ipsum dolor.</p><a href="#">read more</a>
</section>

<div class="tabs">
  <div class="tab active" style="width:116px">Why Us</div>
  <div class="tab" style="width:133px">Copperfleece</div>
  <div class="tab" style="width:133px">Cross Breed</div>
  <div class="tab" style="width:134px">Progency Testing</div>
</div>
<div class="tab-panel">
  <div class="tab-photo" role="img" aria-label="Photo of a Copperfleece ram standing on grass"></div>
  <div class="tab-copy">
    <p>Lorem ipsum dolor sit amet, consectetur adipiscing elit etiam accumsan, ipsum a tristique varius non euismod elit massa vitae odio. Vestibulum sodales nisi quis nisi imperdiet scelerisque euismod ulum elit odio, eu porta metus aenean Lorem ipsum dolor sit amet, consectetur adipiscing elit etiam accumsan, ipsum a tristique varius non euismod elit massa vitae odio.</p>
    <p>Vestibulum sodales nisi quis nisi imperdiet scelerisque euismod ulum elit odio, eu porta metus aenean posuere hendrerit lacus sit amet venenatis. posuere hendrerit lacus sit amet venenatis.Lorem ipsum dolor sit amet, consectetur adipiscing elit etiam accumsan.quis nisi imperdiet scelerisque euismod ulum elit odio, eu porta metus aenean posuere</p>
  </div>
</div>

<div class="sponsors"></div>
<div class="sponsors-title">Our Sponsors</div>
<svg class="sponsor" style="left:161px" width="48" height="28"><rect width="48" height="28" rx="3" fill="#1f6b45"/></svg>
<svg class="sponsor" style="left:252px" width="36" height="40"><rect width="36" height="40" rx="4" fill="#2a67b1"/></svg>
<svg class="sponsor" style="left:331px" width="34" height="45"><rect width="34" height="45" fill="#b5421c"/></svg>
<svg class="sponsor" style="left:398px" width="70" height="14"><rect width="70" height="14" fill="#222"/></svg>
<svg class="sponsor" style="left:486px" width="50" height="28"><rect width="50" height="28" rx="14" fill="#1e3f7a"/></svg>
<svg class="sponsor" style="left:568px" width="64" height="36"><rect width="64" height="36" rx="4" fill="#d2542a"/></svg>
<svg class="sponsor" style="left:682px" width="56" height="44"><rect width="56" height="44" rx="4" fill="#d4b21d"/></svg>
<svg class="sponsor" style="left:750px" width="26" height="26"><circle cx="13" cy="13" r="13" fill="#5aa52c"/></svg>

<footer class="site-footer">
  <nav class="footer-nav"><a href="#">Home</a><span>|</span><a href="#">About Us</a><span>|</span><a href="#">Members</a><span>|</span><a href="#">Stud Pages</a><span>|</span><a href="#">News</a><span>|</span><a href="#">Sales</a><span>|</span><a href="#">Link</a><span>|</span><a href="#">Contact</a></nav>
  <div class="connect"><i></i>Connect with Yardline</div>
  <p class="legal">Copyright © 2014 National Copperfleece Breeders Guild. All rights reserved.<br>Website design and development by Fieldline Studio</p>
</footer>
</body>
</html>
```